Heritage Hollow Business Cards

Require a business card design. <br/><br/>Needs to include logo (either round or long version) plus these details:<br/>Maya Torvell<br/>Heritage Hollow<br/>maya@kelvadtrading.com.au<br/>02 6481 7395<br/>PO Box Glenwarra NSW 2791<br/>www.heritagehollow.com.au<br/><br/>I need in an editable format so that I can create for multiple staff members. <br/><br/>

Target Market(s)

We are an online store selling renovation products to home owners are builders. Looking for a classic classy design.

Industry/Entity Type

Home And Garden

Contact Information for Business Card

Maya Torvell
Heritage Hollow
maya@kelvadtrading.com.au
02 6481 7395
PO Box Glenwarra NSW 2791
www.heritagehollow.com.au

Colors

Designer to choose colors to be used in the design.

Requirements
Must have
• Must include Logo.

```html
<!DOCTYPE html>
<html lang="en">
<head>
<meta charset="utf-8">
<title>Heritage Hollow – Business Card</title>
<link rel="stylesheet" href="https://fonts.googleapis.com/css2?family=Tinos:wght@400;700&display=swap">
<style>
  :root {
    --page-bg: #e9e7e3;
    --card-dark: #1c1a1a;
    --card-light: #f7f7f6;
    --ink: #2a2828;
    --ink-soft: #4a4747;
    --icon-line: #3a3838;
  }
  * { box-sizing: border-box; margin: 0; padding: 0; }
  html, body {
    width: 1200px; height: 780px; overflow: hidden;
    background: var(--page-bg);
    font-family: "Tinos", "Times New Roman", serif;
  }
  .business-card {
    position: absolute; left: 100px; top: 104px;
    width: 1000px; height: 572px;
    background: var(--card-dark);
    border-radius: 6px;
    overflow: hidden;
    box-shadow: 0 10px 30px rgba(0,0,0,.25);
  }
  .card-face { position: absolute; inset: 0; }
  .brand {
    position: absolute; left: 250px; top: 120px;
    display: flex; align-items: center; gap: 18px;
  }
  .brand-mark {
    width: 64px; height: 64px; border-radius: 50%;
    border: 2px solid var(--ink);
  }
  .brand-name {
    font-size: 62px; font-weight: 400; color: var(--ink);
    letter-spacing: .5px; white-space: nowrap;
  }
  .contact-block {
    position: absolute; left: 210px; top: 328px;
    color: var(--ink);
  }
  .person-name { font-size: 30px; font-weight: 400; line-height: 1.1; }
  .person-role { font-size: 21px; color: var(--ink-soft); margin: 2px 0 18px; }
  .contact-list { list-style: none; }
  .contact-item {
    display: flex; align-items: center; gap: 10px;
    font-size: 20px; line-height: 30px; color: var(--ink);
  }
  .contact-icon { width: 20px; height: 20px; flex: none; }
</style>
</head>
<body>
  <div class="business-card">
    <svg class="card-face" viewBox="0 0 1000 572" aria-hidden="true">
      <path d="M 230 0 Q 80 286 230 572 L 770 572 Q 920 286 770 0 Z" fill="var(--card-light)"/>
    </svg>

    <div class="brand">
      <span class="brand-mark"></span>
      <span class="brand-name">Heritage Hollow</span>
    </div>

    <div class="contact-block">
      <p class="person-name">Maya Torvell</p>
      <p class="person-role">Owner</p>
      <ul class="contact-list">
        <li class="contact-item">
          <svg class="contact-icon" viewBox="0 0 20 20"><circle cx="10" cy="10" r="9" fill="none" stroke="var(--icon-line)" stroke-width="1.4"/><path d="M7 5.5 L8.6 5.5 L9.2 8 L8.2 8.8 Q9 11 11.2 11.8 L12 10.8 L14.5 11.4 L14.5 13 Q10 13.5 7.5 10 Q6.5 8 7 5.5Z" fill="var(--icon-line)"/></svg>
          <span>02 6481 7395</span>
        </li>
        <li class="contact-item">
          <svg class="contact-icon" viewBox="0 0 20 20"><circle cx="10" cy="10" r="9" fill="none" stroke="var(--icon-line)" stroke-width="1.4"/><rect x="5.5" y="6.5" width="9" height="7" fill="none" stroke="var(--icon-line)" stroke-width="1.3"/><path d="M5.5 6.5 L10 10.5 L14.5 6.5" fill="none" stroke="var(--icon-line)" stroke-width="1.3"/></svg>
          <span>maya@kelvadtrading.com.au</span>
        </li>
        <li class="contact-item">
          <svg class="contact-icon" viewBox="0 0 20 20"><circle cx="10" cy="10" r="9" fill="none" stroke="var(--icon-line)" stroke-width="1.4"/><path d="M10 15 Q6 10.5 6 8.5 A4 4 0 0 1 14 8.5 Q14 10.5 10 15Z" fill="var(--icon-line)"/><circle cx="10" cy="8.5" r="1.4" fill="var(--card-light)"/></svg>
          <span>PO Box Glenwarra NSW 2791</span>
        </li>
        <li class="contact-item">
          <svg class="contact-icon" viewBox="0 0 20 20"><circle cx="10" cy="10" r="9" fill="none" stroke="var(--icon-line)" stroke-width="1.4"/><circle cx="10" cy="10" r="5" fill="none" stroke="var(--icon-line)" stroke-width="1.2"/><path d="M5 10 H15 M10 5 Q7 10 10 15 M10 5 Q13 10 10 15" fill="none" stroke="var(--icon-line)" stroke-width="1"/></svg>
          <span>www.heritagehollow.com.au</span>
        </li>
      </ul>
    </div>
  </div>
</body>
</html>
```